Ward Compass Business Card Design*

We need a business card design for our company Ward Compass. Our company is specialized in providing online consulting services regarding medical institutions, hospitals and doctors. We work with patients worldwide looking to choose between healthcare providers. We have a website you may use as a reference, where we list doctors and clinics worldwide. So we target Medical providers as well as patients worldwide.
Target Market(s)
Medical Providers and patients around the world
Industry/Entity Type
Medical
Contact Information for Business Card
Salwa Kettani
CEO
+90 612 348 2175
info@wardcompass.example
www.wardcompass.example
14 Annakhil 7 H.R.B. Rabat, Morocco
Requirements
Must have
- Company logo/name on one full side, personal info and smaller logo and company name on the other side.
Nice to have
- Smart and elegant design

```html
<!DOCTYPE html>
<html lang="en">
<head>
<meta charset="utf-8">
<title>Ward Compass — Business Card</title>
<link href="https://fonts.googleapis.com/css2?family=Montserrat:wght@300;400;600;700&display=swap" rel="stylesheet">
<style>
  :root {
    --navy: #123f68;
    --grey: #7b7b7b;
    --ink: #3a3a3a;
    --paper: #ffffff;
    --backdrop: #d9dbde;
  }
  * { box-sizing: border-box; margin: 0; padding: 0; }
  html, body { width: 1200px; height: 800px; overflow: hidden; }
  body {
    background: var(--backdrop);
    font-family: "Montserrat", Arial, sans-serif;
    position: relative;
  }
  .card {
    position: absolute;
    left: 300px;
    width: 600px;
    height: 343px;
    box-shadow: 0 6px 18px rgba(0,0,0,0.18);
  }
  .card--front { top: 36px; background: var(--navy); }
  .card--back { top: 421px; background: var(--paper); }

  .front-wordmark {
    position: absolute;
    left: 0; right: 0; top: 50%;
    transform: translateY(-50%);
    display: flex;
    align-items: center;
    justify-content: center;
    gap: 18px;
  }
  .front-wordmark .dot {
    width: 14px; height: 14px;
    border-radius: 50%;
    background: var(--grey);
  }
  .front-wordmark .name {
    color: var(--paper);
    font-size: 34px;
    font-weight: 600;
    letter-spacing: 1px;
    text-transform: uppercase;
  }

  .back-brand {
    position: absolute;
    left: 48px; top: 42px;
    display: flex;
    align-items: center;
    gap: 12px;
  }
  .back-brand .dot {
    width: 12px; height: 12px;
    border-radius: 50%;
    background: var(--navy);
  }
  .back-brand .name {
    color: var(--navy);
    font-size: 22px;
    font-weight: 600;
    letter-spacing: 0.5px;
    text-transform: uppercase;
  }

  .person { position: absolute; left: 48px; top: 108px; }
  .person .full-name { color: var(--navy); font-size: 19px; font-weight: 700; }
  .person .role { color: var(--ink); font-size: 13px; font-weight: 400; margin-top: 2px; }

  .contacts {
    position: absolute;
    left: 48px; top: 190px;
    list-style: none;
    color: var(--ink);
    font-size: 14px;
    line-height: 23px;
  }
  .contacts li { display: flex; align-items: center; gap: 8px; }
  .contacts svg { width: 13px; height: 13px; flex: none; }
  .contacts .address { margin-top: 8px; }
</style>
</head>
<body>
  <section class="card card--front" aria-label="Card front">
    <div class="front-wordmark">
      <span class="dot"></span>
      <span class="name">Ward Compass</span>
    </div>
  </section>

  <section class="card card--back" aria-label="Card back">
    <div class="back-brand">
      <span class="dot"></span>
      <span class="name">Ward Compass</span>
    </div>

    <div class="person">
      <p class="full-name">Salwa Kettani</p>
      <p class="role">CEO</p>
    </div>

    <ul class="contacts">
      <li>
        <svg viewBox="0 0 16 16" aria-hidden="true"><path fill="#123f68" d="M3.5 1l2.5 3-1.5 2c1 2 2.5 3.5 4.5 4.5l2-1.5 3 2.5-1.5 2.5C7 14 2 9 1 2.5z"/></svg>
        +90 612 348 2175
      </li>
      <li>
        <svg viewBox="0 0 16 16" aria-hidden="true"><rect x="1" y="3" width="14" height="10" fill="none" stroke="#123f68" stroke-width="1.5"/><path d="M1 3l7 6 7-6" fill="none" stroke="#123f68" stroke-width="1.5"/></svg>
        info@wardcompass.example
      </li>
      <li>
        <svg viewBox="0 0 16 16" aria-hidden="true"><circle cx="8" cy="8" r="6.5" fill="none" stroke="#123f68" stroke-width="1.3"/><ellipse cx="8" cy="8" rx="3" ry="6.5" fill="none" stroke="#123f68" stroke-width="1.1"/><path d="M1.5 8h13M2.5 5h11M2.5 11h11" stroke="#123f68" stroke-width="1"/></svg>
        www.wardcompass.example
      </li>
      <li class="address">14 Annakhil 7 H.R.B. Rabat, Morocco</li>
    </ul>
  </section>
</body>
</html>
```